Tech business card design

We need an amazing business card design for our new business 'Pexla' a marketing tech startup based in Sydney, Australia. We provide an online marketplace for businesses to search and buy advertising media, connect with service providers and learn more about marketing. We wish to communicate 'cool tech', reliability and professionalism and design based around our logo.

Target Market(s)

Business Owners

Contact Information for Business Card

Name
Position
Email Address
Website
Phone Number

Font styles to use
Other font styles liked:
• Avenir & Avenir Next

Colors

Designer to choose colors to be used in the design.

```html
<!DOCTYPE html>
<html lang="en">
<head>
<meta charset="UTF-8">
<title>Pexla Business Card</title>
<link href="https://fonts.googleapis.com/css2?family=Nunito+Sans:wght@400;700;800&display=swap" rel="stylesheet">
<style>
  :root {
    --backdrop: #ebebeb;
    --navy: #27244d;
    --paper: #ffffff;
    --ink: #1f1d3d;
    --shadow: rgba(0, 0, 0, 0.12);
  }
  * { margin: 0; padding: 0; box-sizing: border-box; }
  html, body {
    width: 1200px;
    height: 800px;
    overflow: hidden;
    background: var(--backdrop);
    font-family: "Nunito Sans", "Avenir Next", Avenir, sans-serif;
  }
  .canvas {
    position: relative;
    width: 1200px;
    height: 800px;
  }
  .card {
    position: absolute;
    top: 278px;
    width: 419px;
    height: 240px;
    overflow: hidden;
    box-shadow: 0 6px 18px var(--shadow);
  }
  .card--front {
    left: 142px;
    background: var(--navy);
  }
  .card--back {
    left: 638px;
    background: var(--paper);
  }
  .brand-name {
    position: absolute;
    font-weight: 800;
    letter-spacing: -0.01em;
    line-height: 1;
  }
  .card--front .brand-name {
    left: 0;
    right: 0;
    top: 90px;
    text-align: center;
    font-size: 80px;
    color: var(--paper);
  }
  .card--back .brand-name {
    right: 44px;
    top: 160px;
    font-size: 42px;
    color: var(--ink);
  }
  .holder {
    position: absolute;
    left: 36px;
    top: 38px;
    color: var(--ink);
  }
  .holder__name {
    font-size: 20px;
    font-weight: 700;
    letter-spacing: 0.02em;
    line-height: 1.1;
  }
  .holder__role {
    font-size: 15px;
    font-weight: 400;
    line-height: 1.2;
  }
  .contact-list {
    position: absolute;
    left: 38px;
    top: 92px;
    list-style: none;
    color: var(--ink);
    font-size: 15px;
  }
  .contact-list li {
    display: flex;
    align-items: center;
    height: 20.5px;
  }
  .contact-list svg {
    width: 12px;
    height: 12px;
    margin-right: 10px;
    fill: var(--ink);
  }
  .card__band {
    position: absolute;
    left: 0;
    bottom: 0;
    width: 100%;
    height: 30px;
    background: var(--navy);
  }
</style>
</head>
<body>
<main class="canvas">
  <section class="card card--front">
    <div class="brand-name">pexla</div>
  </section>

  <section class="card card--back">
    <div class="holder">
      <div class="holder__name">JOHN SMITH</div>
      <div class="holder__role">General Manager</div>
    </div>
    <ul class="contact-list">
      <li>
        <svg viewBox="0 0 12 12" aria-hidden="true"><circle cx="6" cy="6" r="6"/><path d="M4 3.2l1 1.4-.6.7c.4.9 1.1 1.6 2 2l.7-.6 1.4 1-.5 1.1c-2.2-.2-4.3-2.3-4.5-4.5z" fill="#fff"/></svg>
        012 345 6789
      </li>
      <li>
        <svg viewBox="0 0 12 12" aria-hidden="true"><path d="M0 2.5h12v1L6 7 0 3.5z"/><path d="M0 5l6 3.4L12 5v4.5H0z"/></svg>
        your@email.com
      </li>
      <li>
        <svg viewBox="0 0 12 12" aria-hidden="true"><circle cx="6" cy="6" r="5.5" fill="none" stroke="#1f1d3d" stroke-width="1"/><ellipse cx="6" cy="6" rx="2.3" ry="5.5" fill="none" stroke="#1f1d3d" stroke-width="1"/><path d="M0.5 6h11M1.5 3.3h9M1.5 8.7h9" stroke="#1f1d3d" stroke-width="0.9"/></svg>
        www.website.com
      </li>
    </ul>
    <div class="brand-name">pexla</div>
    <div class="card__band"></div>
  </section>
</main>
</body>
</html>
```